Wren Hollow Farm Postcard Design

I am looking for a new postcard design to mail out this season. We are a Farm business that does wholesale and retail and bulk seasoned firewood sales. we sell firewood from anything from bagged wood to tractor trailer loads of wood. We sell firewood in bulk bags. Pick up or delivery available there is no order to big or too small. I need my business name and phone number on the cards Wren Hollow Farm 615-302-4187 (call or text) I would like it to say we are the best priced guaranteed. I want something that is simple and straight forward but also really catches the eye when they see these in the mail box. I attached my logo and feel free to use photos of split firewood if you would like. id like my email on the card Wrenhollowfarm47@maplepost.net.

Target Market(s)

Firewood purchasers

Industry/Entity Type

agriculture

Requirements
Must have
• email phone number logo

```html
<!DOCTYPE html>
<html lang="en">
<head>
<meta charset="utf-8">
<title>Wren Hollow Farm Postcard</title>
<link href="https://fonts.googleapis.com/css2?family=Oswald:wght@600;700&family=Roboto:wght@400;500;700;900&display=swap" rel="stylesheet">
<style>
  :root {
    --page: #e4e4e4;
    --ember: #6a1804;
    --ember-deep: #4e1203;
    --gold: #f4b63f;
    --flame: #e8402a;
    --orange: #f26b1d;
    --ink: #3b1a10;
    --white: #ffffff;
    --rule: #cfcfcf;
  }
  * { margin: 0; padding: 0; box-sizing: border-box; }
  html, body { width: 913px; height: 1200px; overflow: hidden; background: var(--page); }
  body { position: relative; font-family: "Roboto", sans-serif; }

  .card {
    position: absolute; left: 59px; width: 796px; height: 531px; overflow: hidden;
    box-shadow: 0 2px 8px rgba(0,0,0,0.18);
  }

  /* Front */
  .front { top: 50px; background: radial-gradient(ellipse at 50% 60%, #8a2608 0%, var(--ember) 55%, var(--ember-deep) 100%); }
  .front-photo {
    position: absolute; left: 38px; top: 32px; width: 720px; height: 499px;
    border-top-right-radius: 22px;
    background:
      linear-gradient(180deg, rgba(106,24,4,0) 45%, rgba(120,30,6,0.85) 75%, var(--ember) 92%),
      linear-gradient(90deg, #4f6a3c 0%, #6a2a22 30%, #7b1f1a 55%, #a89680 75%, #d8d8d4 100%);
  }
  .front-frame {
    position: absolute; left: 33px; top: 29px; width: 731px; height: 470px;
    border: 4px solid var(--gold); border-bottom: none;
    border-top-right-radius: 26px;
    -webkit-mask-image: linear-gradient(180deg, #000 60%, transparent 100%);
            mask-image: linear-gradient(180deg, #000 60%, transparent 100%);
  }
  .badge {
    position: absolute; left: -2px; top: -20px; width: 174px; height: 174px;
    border-radius: 50%; background: #050505;
    display: flex; flex-direction: column; align-items: center; justify-content: center;
    padding-top: 18px;
  }
  .badge-name {
    font-family: "Roboto", sans-serif; font-weight: 900; color: var(--gold);
    font-size: 19px; line-height: 21px; text-align: center; text-transform: uppercase;
  }
  .front-title {
    position: absolute; left: 0; right: 0; top: 370px; text-align: center;
    font-family: "Oswald", sans-serif; font-weight: 700; font-size: 42px; letter-spacing: -0.5px;
    text-transform: uppercase;
    background: linear-gradient(180deg, #fff6d8 0%, #ffc24a 45%, #f05a1c 100%);
    -webkit-background-clip: text; background-clip: text; color: transparent;
    filter: drop-shadow(1px 2px 0 rgba(60,10,0,0.7));
  }
  .front-sub {
    position: absolute; left: 0; right: 0; top: 430px; text-align: center;
    color: var(--white); font-weight: 700; font-size: 13px; letter-spacing: 0.3px;
  }
  .front-phone {
    position: absolute; left: 0; right: 0; top: 448px; text-align: center;
    color: var(--gold); font-weight: 900; font-size: 29px; letter-spacing: 1.5px;
  }

  /* Back */
  .back { top: 619px; background: var(--white); }
  .back-panel {
    position: absolute; left: 0; top: 0; width: 398px; height: 531px;
    background: radial-gradient(ellipse at 40% 60%, #7a1e06 0%, var(--ember) 60%, var(--ember-deep) 100%);
  }
  .back-photo {
    position: absolute; left: 0; top: 0; width: 398px; height: 210px;
    background: linear-gradient(90deg, #3a3a3a 0%, #4b2822 40%, #5a1a16 70%, #3e4a30 100%);
  }
  .wave { position: absolute; left: 0; top: 0; width: 398px; height: 240px; }
  .back-title {
    position: absolute; left: 0; width: 398px; top: 34px; text-align: center;
    font-family: "Oswald", sans-serif; font-weight: 700; font-size: 31px; letter-spacing: -0.3px;
    text-transform: uppercase;
    background: linear-gradient(180deg, #fff6d8 0%, #ffc24a 45%, #f05a1c 100%);
    -webkit-background-clip: text; background-clip: text; color: transparent;
    filter: drop-shadow(1px 2px 0 rgba(40,8,0,0.7));
  }
  .shot {
    position: absolute; border-radius: 50%; border: 3px solid var(--white);
  }
  .shot-split { left: 28px; top: 126px; width: 120px; height: 120px; background: linear-gradient(135deg, #6f7a5a 0%, #2f4a2a 50%, #c8962e 100%); }
  .shot-door { left: 112px; top: 99px; width: 94px; height: 94px; background: linear-gradient(135deg, #b02a20 0%, #7a1212 60%, #c98a3a 100%); }
  .shot-rig { left: 195px; top: 98px; width: 76px; height: 76px; background: linear-gradient(180deg, #9fb0c4 0%, #b7a58a 45%, #7a1a18 75%, #6c5a48 100%); }

  .about-head {
    position: absolute; left: 36px; top: 272px;
    font-family: "Oswald", sans-serif; font-weight: 700; font-size: 19px; color: var(--orange);
    text-transform: uppercase;
  }
  .about-text {
    position: absolute; left: 37px; top: 298px; width: 318px;
    color: var(--white); font-size: 11px; line-height: 15.6px;
  }
  .perks { position: absolute; left: 39px; top: 389px; display: flex; }
  .perk { display: flex; align-items: flex-start; gap: 7px; color: var(--white); font-weight: 700; font-size: 11px; line-height: 15.5px; }
  .perk svg { width: 17px; height: 17px; flex: none; margin-top: 3px; }
  .perk:nth-child(1) { width: 98px; }
  .perk:nth-child(2) { width: 106px; }

  .contact-band { position: absolute; left: 0; top: 443px; width: 452px; height: 88px; }
  .contacts { position: absolute; left: 18px; top: 474px; display: flex; }
  .contact { display: flex; gap: 7px; }
  .contact:nth-child(1) { width: 125px; }
  .contact:nth-child(2) { width: 178px; }
  .contact-icon {
    width: 32px; height: 32px; border-radius: 50%; background: var(--ember);
    display: flex; align-items: center; justify-content: center; flex: none;
  }
  .contact-icon svg { width: 11px; height: 11px; }
  .contact-label { font-weight: 700; font-size: 11px; color: var(--ink); margin-bottom: 3px; }
  .contact-value { font-size: 8.8px; line-height: 13px; color: var(--ink); }

  .stamp-box { position: absolute; left: 683px; top: 25px; width: 90px; height: 94px; border: 1px solid var(--rule); }
  .address-line { position: absolute; left: 436px; width: 340px; height: 1px; background: var(--rule); }
</style>
</head>
<body>

<section class="card front">
  <div class="front-photo" role="img" aria-label="Photo of the farm's red tractor-trailer cab parked in front of a tan steel barn"></div>
  <div class="front-frame"></div>
  <div class="badge">
    <div class="badge-name">Wren Hollow<br>Farm</div>
  </div>
  <h1 class="front-title">Wren Hollow Farm</h1>
  <p class="front-sub">CARDS WREN HOLLOW FARM</p>
  <p class="front-phone">615-302-4187</p>
</section>

<section class="card back">
  <div class="back-panel">
    <div class="back-photo" role="img" aria-label="Darkened photo of the farm truck beside the barn"></div>
    <svg class="wave" viewBox="0 0 398 240" preserveAspectRatio="none">
      <path d="M0 190 C60 150 170 122 267 128 C320 132 370 150 398 178 L398 240 L0 240 Z" fill="var(--ember)"/>
      <path d="M267 128 C320 132 370 150 398 178 L398 190 C370 162 320 142 267 136 Z" fill="var(--gold)"/>
      <path d="M0 192 C20 180 40 170 60 163 L60 170 C40 177 20 188 0 200 Z" fill="var(--flame)"/>
      <path d="M0 186 C60 146 170 118 267 124 C320 128 370 146 398 174 L398 178 C370 150 320 132 267 128 C170 122 60 150 0 190 Z" fill="var(--white)"/>
    </svg>
    <h2 class="back-title">Wren Hollow Farm</h2>
    <div class="shot shot-split" role="img" aria-label="Photo of a firewood processor splitting logs"></div>
    <div class="shot shot-door" role="img" aria-label="Close-up photo of the lettered truck door"></div>
    <div class="shot shot-rig" role="img" aria-label="Photo of the truck parked at the barn"></div>

    <h3 class="about-head">Who We Are</h3>
    <p class="about-text">Lorem ipsum dolor sit amet, consectetur adipiscing elit, sed do eiusmod tempor incididunt ut labore et dolore magna aliqua. Ut enim ad minim veniam, quis nostrud exercitation ullamco laboris nisi ut aliquip ex ea commodo consequat.</p>

    <div class="perks">
      <div class="perk">
        <svg viewBox="0 0 20 20"><circle cx="9" cy="11" r="7.5" fill="none" stroke="var(--orange)" stroke-width="1.8"/><path d="M5.5 10.5 L8.5 14 L17 3" fill="none" stroke="var(--orange)" stroke-width="2" stroke-linecap="round" stroke-linejoin="round"/></svg>
        <span>Licensed<br>Arborists</span>
      </div>
      <div class="perk">
        <svg viewBox="0 0 20 20"><circle cx="9" cy="11" r="7.5" fill="none" stroke="var(--orange)" stroke-width="1.8"/><path d="M5.5 10.5 L8.5 14 L17 3" fill="none" stroke="var(--orange)" stroke-width="2" stroke-linecap="round" stroke-linejoin="round"/></svg>
        <span>Competitive<br>Pricing</span>
      </div>
      <div class="perk">
        <svg viewBox="0 0 20 20"><circle cx="9" cy="11" r="7.5" fill="none" stroke="var(--orange)" stroke-width="1.8"/><path d="M5.5 10.5 L8.5 14 L17 3" fill="none" stroke="var(--orange)" stroke-width="2" stroke-linecap="round" stroke-linejoin="round"/></svg>
        <span>Free<br>Estimates</span>
      </div>
    </div>
  </div>

  <svg class="contact-band" viewBox="0 0 452 88" preserveAspectRatio="none">
    <path d="M0 0 L398 0 C430 4 450 30 452 60 L452 88 L0 88 Z" fill="var(--flame)"/>
    <path d="M0 8 L396 8 C424 12 446 36 446 66 L446 88 L0 88 Z" fill="var(--gold)"/>
  </svg>

  <div class="contacts">
    <div class="contact">
      <div class="contact-icon"><svg viewBox="0 0 12 12"><path d="M6 0.8 C3.8 0.8 2.3 2.4 2.3 4.4 C2.3 7 6 11.2 6 11.2 C6 11.2 9.7 7 9.7 4.4 C9.7 2.4 8.2 0.8 6 0.8 Z" fill="var(--white)"/><circle cx="6" cy="4.4" r="1.4" fill="var(--ember)"/></svg></div>
      <div>
        <p class="contact-label">Address :</p>
        <p class="contact-value">214 Birchline Rd<br>Ashford TN 37015</p>
      </div>
    </div>
    <div class="contact">
      <div class="contact-icon"><svg viewBox="0 0 12 12"><rect x="1" y="2.5" width="10" height="7" rx="1" fill="var(--white)"/><path d="M1.3 3 L6 6.6 L10.7 3" fill="none" stroke="var(--ember)" stroke-width="1"/></svg></div>
      <div>
        <p class="contact-label">Email Address :</p>
        <p class="contact-value">Wrenhollowfarm47@maplepost.net</p>
      </div>
    </div>
    <div class="contact">
      <div class="contact-icon"><svg viewBox="0 0 12 12"><path d="M3 1 L4.8 3.6 L3.8 4.8 C4.5 6.3 5.7 7.5 7.2 8.2 L8.4 7.2 L11 9 L10 11 C5.5 10.8 1.2 6.5 1 2 Z" fill="var(--white)"/></svg></div>
      <div>
        <p class="contact-label">Phone :</p>
        <p class="contact-value">615-302-4187</p>
      </div>
    </div>
  </div>

  <div class="stamp-box"></div>
  <div class="address-line" style="top:184px"></div>
  <div class="address-line" style="top:224px"></div>
  <div class="address-line" style="top:260px"></div>
  <div class="address-line" style="top:299px"></div>
  <div class="address-line" style="top:335px"></div>
</section>

</body>
</html>
```